Dashboard Elements

Hello – looking for someone to create dashboard elements.
I’ve already basically designed all these elements – but I need someone to take what I’ve designed and make it look like an actual dashboard UI, like an app - assuming using some kind of dashboard UI kit (but however you would like to get it done is fine). It can look just like mine or try something different, as long as it matches the color scheme webpage that I’m going to out it on – see the page here. I’m ok with making it dark, maybe that would look better – again as long as it matches the webpage (https://www.plandeck.io/file/7QxKtr2BwLpZnVe4Hs8Mc1/Webpage-with-placeholders?node-id=0%3A1). Please note, you do not need to put anything on the webpage or do anything with this Figma file, this is just a reference so you can color/stylize it accordingly.

The attached Powerpoint file has everything you need - make sure to zoom all the way out to see everything on the slides.

Here are the Dashboard elements needed (this will all make sense when you look at the PPT):
Dashboard 1
Dashboard 1 – expanded view A
Dashboard 1 – expanded view B
View Source button by itself
Source Document Viewer 1 and 2 (these are exactly the same just with a different image inside)*
Dashboard 2 (only slightly different than Dashboard 1, just extended with extra headings
Table of Contents
Searchbar and Source Doc by itself
*the documents in the source document viewers should still look like documents - they don’t need to look like part of the UI, because this is a document viewer – you can restyle/recolor if necessary or just leave these as is.
- Colors must match color scheme of webpage, attached and on Figma link (images there currently are only placeholders) – ok to go dark as long as it matches
- Must look sleek, clean, realistic
- Don’t add any pictures of people or change the text.
- In case it’s not clear, this is what I mean by the concept of Dashboard UI - https://www.notavia.net/shard/s7/sh/8fad21bc-14e9-4a7c-b2d0-5c3e9f71a604/92c4e1b7a05d3f68e1c2b947d0a3f815
- Must be sent in an editable file, I may need to be edit text and other elements
- If you are going to send a sample, please make sure it’s part of the dashboard itself, not just the table of contents etc

Ideally hoping to find someone I can continue working with as I'll have a lot more graphic design work needed coming up.

Thank you!

```html
<!DOCTYPE html>
<html lang="en">
<head>
<meta charset="utf-8">
<title>CareLedger – C-CDA Compendium</title>
<link href="https://fonts.googleapis.com/css2?family=Poppins:wght@400;500;600&display=swap" rel="stylesheet">
<style>
:root{
  --stage:#100e22;
  --shell:#15132b;
  --panel:#1f1c3a;
  --row-a:#38365f;
  --row-b:#2c2a51;
  --thead:#16142c;
  --field:#2c2a4d;
  --teal:#2ec4c6;
  --green:#22c7a9;
  --blue:#1d78d4;
  --purple:#7a5ce2;
  --text:#e9e8f4;
  --muted:#b9b7d2;
}
*{box-sizing:border-box;margin:0;padding:0}
html,body{width:1200px;height:2411px;overflow:hidden}
body{background:var(--stage);font-family:'Poppins',sans-serif;color:var(--text);position:relative}
.dashboard{position:absolute;left:0;top:587px;width:1200px;height:1237px;background:var(--shell)}
.topbar{height:98px;display:flex;align-items:center;padding:0 38px 0 52px}
.brand-mark{width:36px;height:36px;background:var(--purple);border-radius:6px;margin-right:42px}
.brand-name{font-size:26px;font-weight:500;color:var(--green);line-height:1}
.brand-tag{font-size:11.5px;font-weight:500;letter-spacing:.3px;margin-top:8px}
.top-actions{margin-left:auto;display:flex;align-items:center;gap:26px}
.bell{background:var(--blue);border-radius:12px;padding:3px 10px;font-size:10px;font-weight:600;display:flex;gap:4px;align-items:center;box-shadow:0 0 12px var(--teal)}
.user{display:flex;align-items:center;gap:10px;font-size:12.5px}
.avatar{width:24px;height:24px;border-radius:4px;background:linear-gradient(135deg,#d9c8c0,#7d6a6a)}
.sidebar{position:absolute;left:0;top:98px;width:231px;padding:18px 36px}
.nav-group{font-size:15px;font-weight:500;margin:0 0 12px}
.nav-group.support{margin-top:28px}
.nav-item{display:flex;align-items:center;gap:10px;height:38px;margin-bottom:8px;font-size:15px}
.nav-ico{width:38px;height:38px;border-radius:8px;background:#25233f;display:flex;align-items:center;justify-content:center}
.nav-item.active{color:var(--green);font-weight:500}
.nav-item.active .nav-ico{background:#24304a}
.main{position:absolute;left:231px;top:98px;width:969px;height:1072px;background:var(--panel);padding:18px 29px 0}
.crumbs{display:flex;align-items:center;height:38px}
.crumb-ico{width:38px;height:38px;border-radius:8px;background:#34325a;display:flex;align-items:center;justify-content:center;margin-right:10px}
.crumb-link{color:var(--teal);font-size:19px}
.crumb-cur{font-size:19px;font-weight:600}
.finder{margin-left:auto;display:flex;gap:16px;align-items:center}
.print{width:38px;height:34px;border-radius:6px;background:#34325a;display:flex;align-items:center;justify-content:center}
.id-search{width:283px;height:34px;background:var(--field);border-radius:4px;display:flex;align-items:center;padding:0 4px 0 14px;font-size:14px;color:var(--muted)}
.id-search .type{margin-left:auto;color:var(--teal);font-size:11.5px;border-left:1px solid var(--muted);padding-left:6px;margin-right:10px}
.go{width:26px;height:26px;border-radius:4px;background:var(--blue);display:flex;align-items:center;justify-content:center}
.profile{display:flex;margin-top:20px;font-size:17px;align-items:baseline}
.profile .label{color:var(--green);font-weight:500;margin-right:12px}
.profile .updated{margin-left:auto}
.cards{display:flex;gap:27px;margin-top:12px}
.stat{width:150px;height:57px;border-radius:5px;display:flex;align-items:center;justify-content:space-between;padding:0 18px}
.stat small{display:block;font-size:12px}
.stat b{font-size:13px;font-weight:600;letter-spacing:1px}
.stat.raf{background:linear-gradient(90deg,var(--blue),var(--teal))}
.stat.raf small{letter-spacing:3px}
.stat.raf b{letter-spacing:4px}
.stat.cond{background:linear-gradient(90deg,var(--green),#4bd0c6)}
.stat.idn{background:linear-gradient(90deg,var(--purple),#9b86ee)}
.stat-ico{width:34px;height:34px;border-radius:50%;background:#1f2147;display:flex;align-items:center;justify-content:center}
.section-title{margin-top:30px;color:var(--teal);font-size:19px;font-weight:500;display:flex;align-items:center;gap:6px}
.table-head{display:flex;align-items:center;justify-content:space-between;margin-top:6px;height:36px}
.table-head h3{font-size:15px;font-weight:600;align-self:flex-end}
.search{width:174px;height:34px;background:var(--field);border-radius:4px;display:flex;align-items:center;padding:0 4px 0 18px;font-size:12px;justify-content:space-between}
.codes{width:903px;margin-top:10px;font-size:12px}
.codes .tr{display:grid;grid-template-columns:119px 461px 116px 92px 115px;align-items:center;height:47px;padding-left:19px}
.codes .th{background:var(--thead);font-size:11.5px;font-weight:500}
.codes .tr:nth-child(even){background:var(--row-a)}
.codes .tr:nth-child(odd):not(.th){background:var(--row-b)}
.code,.raf{color:var(--teal)}
.detail{width:83px;height:28px;border-radius:3px;background:linear-gradient(90deg,var(--blue),var(--teal));display:flex;align-items:center;justify-content:space-around;padding:0 6px;font-size:12.5px}
.pager{display:flex;justify-content:flex-end;align-items:center;gap:8px;width:903px;margin-top:12px;font-size:12px;padding-right:14px}
.rows-sel{background:var(--field);padding:5px 7px;border-radius:3px;margin-right:30px}
.pg{width:33px;height:28px;border-radius:3px;display:flex;align-items:center;justify-content:center;background:#2b2950}
.pg.next{background:var(--blue)}
.gap{height:40px}
.footer{position:absolute;left:260px;right:38px;top:1190px;display:flex;justify-content:space-between;font-size:15px}
.footer .brand{color:var(--green)}
</style>
</head>
<body>
<div class="dashboard">
  <header class="topbar">
    <div class="brand-mark"></div>
    <div>
      <div class="brand-name">CareLedger</div>
      <div class="brand-tag">EACH PATIENTS' FULL MEDICAL HISTORY, SUMMARY AND ANALYSIS IN ONE COMPREHENSIVE HEALTH RECORD</div>
    </div>
    <div class="top-actions">
      <svg width="18" height="18" viewBox="0 0 18 18" fill="#7f7cf0"><circle cx="2" cy="2" r="2"/><circle cx="9" cy="2" r="2"/><circle cx="16" cy="2" r="2"/><circle cx="2" cy="9" r="2"/><circle cx="9" cy="9" r="2"/><circle cx="16" cy="9" r="2"/><circle cx="2" cy="16" r="2"/><circle cx="9" cy="16" r="2"/><circle cx="16" cy="16" r="2"/></svg>
      <div class="bell"><svg width="9" height="10" viewBox="0 0 9 10" fill="#fff"><path d="M4.5 0C2.5 0 1.5 1.6 1.5 3.5V6L0 8h9L7.5 6V3.5C7.5 1.6 6.5 0 4.5 0zM3.3 9h2.4a1.2 1.2 0 01-2.4 0z"/></svg>27</div>
      <div class="user"><div class="avatar" role="img" aria-label="User profile photo"></div>Lena Admin <svg width="8" height="5" viewBox="0 0 8 5" fill="#fff"><path d="M0 0h8L4 5z"/></svg></div>
    </div>
  </header>

  <nav class="sidebar">
    <div class="nav-group">Main</div>
    <div class="nav-item"><span class="nav-ico"><svg width="16" height="16" viewBox="0 0 16 16" fill="#fff"><rect width="7" height="9"/><rect x="9" width="7" height="5"/><rect y="11" width="7" height="5"/><rect x="9" y="7" width="7" height="9"/></svg></span>Dashboard</div>
    <div class="nav-item"><span class="nav-ico"><svg width="18" height="14" viewBox="0 0 18 14" fill="#fff"><circle cx="6" cy="4" r="3.5"/><circle cx="13" cy="4" r="3"/><path d="M0 14c0-4 3-6 6-6s6 2 6 6zM13 8c3 0 5 2 5 5h-5z"/></svg></span>Employee</div>
    <div class="nav-item"><span class="nav-ico"><svg width="12" height="16" viewBox="0 0 12 16" fill="#fff"><path d="M0 0h8l4 4v12H0z"/></svg></span>Document</div>
    <div class="nav-item"><span class="nav-ico"><svg width="16" height="16" viewBox="0 0 16 16" fill="#fff"><rect y="2" width="16" height="14" rx="1"/><rect x="3" width="2" height="4"/><rect x="11" width="2" height="4"/><rect x="1" y="6" width="14" height="1" fill="#25233f"/></svg></span>Appointment</div>
    <div class="nav-item"><span class="nav-ico"><svg width="16" height="16" viewBox="0 0 16 16" fill="#fff"><path d="M2 3l11 4-2 4-9-4zM5 9l-2 5M1 14h4"/><path d="M5 9l-2 5" stroke="#fff" stroke-width="2"/></svg></span>Surveillance</div>
    <div class="nav-item active"><span class="nav-ico"><svg width="16" height="16" viewBox="0 0 16 16" fill="#22c7a9"><rect width="7" height="7" rx="1.5"/><rect x="9" width="7" height="7" rx="1.5"/><rect y="9" width="7" height="7" rx="1.5"/><rect x="9" y="9" width="7" height="7" rx="1.5"/></svg></span>Reports</div>
    <div class="nav-group support">Support</div>
    <div class="nav-item"><span class="nav-ico"><svg width="16" height="16" viewBox="0 0 16 16"><circle cx="8" cy="8" r="6" fill="#fff"/><circle cx="8" cy="8" r="2.3" fill="#25233f"/></svg></span>Settings</div>
    <div class="nav-item"><span class="nav-ico"><svg width="18" height="18" viewBox="0 0 18 18"><circle cx="9" cy="9" r="9" fill="#fff"/><text x="9" y="13.5" font-size="12" font-weight="700" text-anchor="middle" fill="#25233f" font-family="Poppins,sans-serif">?</text></svg></span>Tutorial</div>
  </nav>

  <main class="main">
    <div class="crumbs">
      <span class="crumb-ico"><svg width="16" height="16" viewBox="0 0 16 16" fill="#22c7a9"><rect width="7" height="7" rx="1.5"/><rect x="9" width="7" height="7" rx="1.5"/><rect y="9" width="7" height="7" rx="1.5"/><rect x="9" y="9" width="7" height="7" rx="1.5"/></svg></span>
      <span class="crumb-link">Reports</span>
      <svg width="10" height="12" viewBox="0 0 10 12" fill="#2ec4c6" style="margin:0 4px"><path d="M0 0l10 6-10 6z"/></svg>
      <span class="crumb-cur">C-CDA Compendium</span>
      <div class="finder">
        <span class="print"><svg width="16" height="15" viewBox="0 0 16 15" fill="#2ec4c6"><rect x="4" width="8" height="4"/><rect y="5" width="16" height="6" rx="1"/><rect x="4" y="9" width="8" height="6"/></svg></span>
        <div class="id-search">Type ID Number here <span class="type">ID Number ▾</span><span class="go"><svg width="14" height="14" viewBox="0 0 14 14" fill="none" stroke="#fff" stroke-width="2"><circle cx="6" cy="6" r="4.5"/><path d="M9.5 9.5L13 13"/></svg></span></div>
      </div>
    </div>

    <div class="profile"><span class="label">Patient Profile</span>Ana Rowe | Female | 70 Years Old | 01-11-1951<span class="updated"><span style="color:var(--green)">Last Updated:</span> May 24, 2021</span></div>

    <div class="cards">
      <div class="stat raf"><div><small>RAF</small><b>1.462</b></div><span class="stat-ico"><svg width="14" height="14" viewBox="0 0 14 14" fill="#2ec4c6"><circle cx="6" cy="4" r="3"/><path d="M0 13c0-3 3-5 6-5s6 2 6 5z"/></svg></span></div>
      <div class="stat cond"><div><small>Condition</small><b>5</b></div><span class="stat-ico"><svg width="14" height="14" viewBox="0 0 14 14" fill="#22c7a9"><circle cx="6" cy="4" r="3"/><path d="M0 13c0-3 3-5 6-5s6 2 6 5z"/><path d="M11 6h3M12.5 4.5v3" stroke="#22c7a9"/></svg></span></div>
      <div class="stat idn"><div><small>ID Number</small><b>7326472</b></div><span class="stat-ico"><svg width="14" height="14" viewBox="0 0 14 14" fill="#fff"><circle cx="7" cy="4" r="3"/><path d="M1 13c0-3 3-5 6-5s6 2 6 5z"/></svg></span></div>
    </div>

    <div class="section-title"><svg width="16" height="10" viewBox="0 0 16 10" fill="#2ec4c6"><path d="M0 0h16L8 10z"/></svg>HCC Summary</div>

    <div class="table-head"><h3>Newly Identified ICD-10 Code</h3><div class="search">Search<span class="go"><svg width="14" height="14" viewBox="0 0 14 14" fill="none" stroke="#fff" stroke-width="2"><circle cx="6" cy="6" r="4.5"/><path d="M9.5 9.5L13 13"/></svg></span></div></div>
    <div class="codes">
      <div class="tr th"><span>ICD-10 CODE ▾</span><span>CONDITION ▾</span><span>CATEGORY ▾</span><span>RAF ▾</span><span>ACTION</span></div>
      <div class="tr"><span class="code">170.0</span><span>Aortic Atherosclerosis</span><span>108</span><span class="raf">0.298</span><span class="detail">Detail ▾</span></div>
      <div class="tr"><span class="code">F33.1</span><span>Major Deppresive Disorder, Recurrent, Moderate</span><span>58</span><span class="raf">0.309</span><span class="detail">Detail ▾</span></div>
      <div class="tr"><span class="code">148.2</span><span>Chronic Atrial Fibrillation</span><span>96</span><span class="raf">0.268</span><span class="detail">Detail ▾</span></div>
      <div class="tr"><span class="code">120.9</span><span>Angina Pectoris</span><span>88</span><span class="raf">0.140</span><span class="detail">Detail ▾</span></div>
    </div>
    <div class="pager">Show Row <span class="rows-sel">5 ▾</span><span class="pg">◀</span><span class="pg next">▶</span></div>

    <div class="gap"></div>
    <div class="table-head"><h3>Previously Known ICD-10 Code</h3><div class="search">Search<span class="go"><svg width="14" height="14" viewBox="0 0 14 14" fill="none" stroke="#fff" stroke-width="2"><circle cx="6" cy="6" r="4.5"/><path d="M9.5 9.5L13 13"/></svg></span></div></div>
    <div class="codes">
      <div class="tr th"><span>ICD-10 CODE ▾</span><span>CONDITION ▾</span><span>CATEGORY ▾</span><span>RAF ▾</span><span>ACTION</span></div>
      <div class="tr"><span class="code">F32.9</span><span>Major Deppresive Disorder, Single Episode, Unspecified</span><span>N/A</span><span class="raf">0</span><span class="detail">Detail ▾</span></div>
      <div class="tr"><span class="code">Z79.01</span><span>Long Term Use of Anticoagulants</span><span>N/A</span><span class="raf">0</span><span class="detail">Detail ▾</span></div>
      <div class="tr"><span class="code">125.9</span><span>Chronic Ischemic Heart Disease, Unspecified</span><span>N/A</span><span class="raf">0</span><span class="detail">Detail ▾</span></div>
      <div class="tr"><span class="code">D45</span><span>Polycythemia Vera</span><span>48</span><span class="raf">0.312</span><span class="detail">Detail ▾</span></div>
      <div class="tr"><span class="code">F32.9</span><span>Hypertensive Heart Disease</span><span>N/A</span><span class="raf">3.239</span><span class="detail">Detail ▾</span></div>
      <div class="tr"><span class="code">120.9</span><span>Type 2 Diabetes Mellitus</span><span>N/A</span><span class="raf">1.060</span><span class="detail">Detail ▾</span></div>
    </div>
    <div class="pager">Show Row <span class="rows-sel">6 ▾</span><span class="pg">◀</span><span class="pg next">▶</span></div>
  </main>

  <footer class="footer"><span>© 2021 - All Rights Licensed</span><span class="brand">CareLedger</span></footer>
</div>
</body>
</html>
```